home accents e-commerce website

I'd like a professional simple website designed where I can sell my home goods. I already have my domain name registered. I need the website to accept credit card payments and Monvex. It should have a shopping cart option and calculate sales tax and shipping costs on merchandise automatically.

I'll be taking photographs of the merchandise and writing product descriptions myself. (I'm not a professional photographer, so these photos probably won't look too polished. If you can help me make them look better, that'd be great). As I add new merchandise in the future, I'd like an option where I can log in to the back end myself and add pictures/product descriptions. And take old products down as they sell out. So the website needs to be user-friendly for me, even though I'm completely web design illiterate!

I'd like a creative, talented person who can create a whimsical, cute website. Nothing too corporate-looking.

Thank you!

Target Market(s)

women, online shoppers, New York City-area, (ship products to the United States only)

Industry/Entity Type

Home And Garden

Coding

Coded - Design and coding required

Number of Pages Required

1 page

Font styles to use
Sans Serif

Colors
0355a3
ffffff

Requirements
Must have
• shopping cart feature
• safe, secure credit card and Monvex payments
• ability for me to go in and add new products and take down old/sold products
Nice to have
• whimsical, cute design
Should not have
• too corporate-looking

```html
<!DOCTYPE html>
<html lang="en">
<head>
<meta charset="utf-8">
<title>Hollis Home Goods</title>
<link href="https://fonts.googleapis.com/css2?family=Raleway:wght@400;500;600;700&family=Oswald:wght@300&display=swap" rel="stylesheet">
<style>
:root{
  --blue:#0355a3;
  --white:#ffffff;
  --ink:#222;
  --muted:#8a8a8a;
  --line:#dcdcdc;
  --sidebar:#f4f4f4;
  --footer:#f1f1f1;
}
*{margin:0;padding:0;box-sizing:border-box}
html,body{width:762px;height:1200px;overflow:hidden;background:var(--white)}
body{position:relative;font-family:"Raleway",sans-serif;color:var(--ink)}
.abs{position:absolute}
.brand{font-family:"Raleway",sans-serif;color:var(--blue);font-weight:700;letter-spacing:1px}
.brand .name{display:block;font-size:30px;line-height:30px}
.brand .tag{display:block;font-size:9px;letter-spacing:6px;font-weight:700;margin-top:2px}

.main-nav{left:211px;top:19px;height:25px;border:1px solid var(--line);display:flex;font-size:7px;font-weight:600;letter-spacing:.3px}
.main-nav a{color:#333;text-decoration:none;padding:0 10px;line-height:23px;border-right:1px solid var(--line)}
.main-nav a:last-child{border-right:0}
.tagline{left:211px;top:54px;color:var(--blue);font-size:13px;font-weight:500}
.social{left:499px;top:24px;display:flex;align-items:center;gap:3px;font-size:6px;color:#444}
.social span.dot{width:18px;height:18px;border:1px solid var(--blue);border-radius:50%;display:inline-block}
.social .label{margin-right:2px}
.cart{left:640px;top:19px;width:35px;height:25px;background:var(--blue)}
.cart .count{position:absolute;right:-4px;top:-4px;width:11px;height:11px;border-radius:50%;background:var(--white);border:1px solid var(--blue);font-size:7px;line-height:9px;text-align:center;color:var(--blue);font-weight:700}
.rule{left:0;top:79px;width:762px;height:2px;background:var(--blue)}

.sidebar{left:0;top:81px;width:192px;height:308px;background:var(--sidebar)}
.sidebar h3{background:var(--blue);color:var(--white);font-size:9px;font-weight:600;height:29px;line-height:29px;padding-left:11px}
.sidebar ul{list-style:none;padding:0 9px 0 12px}
.sidebar li{height:30px;border-bottom:1px solid var(--line);display:flex;align-items:center;font-size:6.5px;color:#444}
.sidebar li:last-child{border-bottom:0}
.sidebar li i{width:6px;height:6px;border:1px solid #aaa;margin-right:7px;font-style:normal;font-size:5px;line-height:4px;text-align:center;color:#888}
.sidebar li b{margin-left:auto;font-weight:400}

.hero{left:192px;top:81px;width:570px;height:308px;background:linear-gradient(100deg,#e9e4dc 0%,#c9b9a2 35%,#8b6a4b 60%,#b89e84 80%,#ece6de 100%)}
.hero-title{left:455px;top:177px;width:223px;height:41px;background:rgba(30,30,30,.78);color:var(--white);font-family:"Oswald",sans-serif;font-weight:300;font-size:21px;line-height:41px;padding-left:16px}
.hero-copy{left:470px;top:219px;width:208px;height:48px;background:rgba(30,30,30,.7);color:var(--white);font-size:8px;line-height:13px;padding:9px 9px 0 9px}
.hero-btn{left:603px;top:270px;width:74px;height:21px;background:var(--blue);color:var(--white);font-size:6.5px;font-weight:700;text-align:center;line-height:21px}

.section-title{left:0;top:418px;width:762px;text-align:center;font-size:15px;font-weight:700}
.section-sub{left:195px;top:438px;width:372px;text-align:center;font-size:5px;line-height:12px;color:#555}

.card{width:138px}
.card .pic{height:123px;border:1px solid var(--line);position:relative;display:flex;align-items:center;justify-content:center}
.card .pic div{width:70px;height:90px;border-radius:8px}
.card .pic svg{position:absolute;right:7px;top:7px}
.card h4{font-size:7.5px;font-weight:600;margin-top:9px}
.card p{font-size:6.5px;line-height:12px;color:var(--muted);margin-top:2px}
.card .price{color:var(--blue);font-weight:700;font-size:9.5px;margin-top:6px}

.perks{left:0;top:923px;width:762px;height:109px;background:var(--blue);color:var(--white)}
.perk{position:absolute;top:27px;display:flex}
.perk .ico{width:38px;height:38px;border:2px solid var(--white);border-radius:50%;display:flex;align-items:center;justify-content:center;margin-right:12px;flex:none}
.perk h5{font-size:8px;letter-spacing:.6px;font-weight:600;margin-top:3px}
.perk p{font-size:6.3px;line-height:12px;margin-top:4px;width:130px}
.perk-sep{position:absolute;top:15px;width:1px;height:80px;background:rgba(255,255,255,.25)}

.footer{left:0;top:1032px;width:762px;height:168px;background:var(--footer)}
.fcol{position:absolute;top:25px;font-size:6.5px;color:var(--muted)}
.fcol h6{font-size:7.5px;color:#333;font-weight:700;margin-bottom:9px}
.fcol li{list-style:none;line-height:13.2px}
.newsletter input{display:block;width:128px;height:21px;border:1px solid var(--line);background:var(--white);font:6.5px "Raleway",sans-serif;padding-left:8px;margin-top:8px}
.newsletter .btn{display:block;width:62px;height:19px;background:var(--blue);color:var(--white);font-size:6.5px;font-weight:700;text-align:center;line-height:19px;margin-top:8px}
.contact-line{display:flex;align-items:center;gap:5px}
.fbar{left:83px;top:1159px;width:595px;height:1px;background:var(--line)}
.copy{left:83px;top:1174px;font-size:6.5px;color:#555}
.pay{left:574px;top:1165px;display:flex;align-items:center;gap:6px;font-size:6.5px;color:#555}
.pay span.c{width:25px;height:25px;border:1px solid #555;border-radius:50%;display:flex;align-items:center;justify-content:center;font-size:5px;font-weight:700;color:#555}
</style>
</head>
<body>

<header>
  <div class="abs brand" style="left:42px;top:20px"><span class="name">hollis</span><span class="tag">HOME GOODS</span></div>
  <nav class="abs main-nav"><a>ABOUT HOLLIS</a><a>HOW DOES THIS CRAZINESS WORK?</a><a>CONTACT</a></nav>
  <div class="abs tagline">Brookfield Design Delivery Service</div>
  <div class="abs social"><span class="label">SOCIAL MEDIA :</span><span class="dot"></span><span class="dot"></span><span class="dot"></span><span class="dot"></span></div>
  <div class="abs cart">
    <svg width="35" height="25" viewBox="0 0 35 25"><path d="M11 8h3l2 8h8l2-6H15" fill="none" stroke="#fff" stroke-width="1.6"/><circle cx="17" cy="18.5" r="1.3" fill="#fff"/><circle cx="23" cy="18.5" r="1.3" fill="#fff"/></svg>
    <span class="count">0</span>
  </div>
  <div class="abs rule"></div>
</header>

<aside class="abs sidebar">
  <h3>CATEGORY</h3>
  <ul>
    <li><i>+</i>VASES AND DECORATIVE BOWLS<b>(16)</b></li>
    <li><i>+</i>THROW PILLOWS<b>(26)</b></li>
    <li><i>+</i>BLANKETS, THROWS, SHAWLS<b>(9)</b></li>
    <li><i>+</i>FOR YOUR FLOORS<b>(5)</b></li>
    <li><i>+</i>FOR YOUR WALLS<b>(3)</b></li>
    <li><i>+</i>FOR YOUR TABLE<b>(9)</b></li>
    <li><i>+</i>FOR YOUR BEDSIDE<b>(1)</b></li>
    <li><i>+</i>LET THERE BE LIGHT<b>(4)</b></li>
    <li><i>+</i>PUT YOUR FEET UP<b>(2)</b></li>
  </ul>
</aside>

<section class="abs hero" role="img" aria-label="Bright kitchen interior with wooden bar stools and pendant lights"></section>
<div class="abs hero-title">WE SELLING  HOME GOODS</div>
<div class="abs hero-copy">Lorem ipsum dolor amet, consectetur adipiscing sed do eiusmod tempor incididunt</div>
<div class="abs hero-btn">ADD TO CART</div>

<h2 class="abs section-title">FEATURE PRODUCTS</h2>
<p class="abs section-sub">LOREM IPSUM DOLOR SIT AMET, CONSECTETUR ADIPISCING ELIT, SED DO EIUSMOD TEMPOR INCIDIDUNT UT LABORE ET DOLORE MAGNA ALIQUA. UT ENIM AD MINIM VENIAM, QUIS NOSTRUD EXERCITATION</p>

<div class="abs card" style="left:83px;top:487px"><div class="pic"><div role="img" aria-label="Blue and white porcelain vase" style="background:linear-gradient(#3a62a8,#d9e0f0,#c94a4a)"></div><svg width="13" height="11"><path d="M1 2h2l2 6h6l1-4H4" fill="none" stroke="#999"/></svg></div><h4>CUPIDATAT</h4><p>Lorem ipsum dolor sit amet, consectetur adipiscing elit, sed do eiusmod...</p><div class="price">$29.99</div></div>
<div class="abs card" style="left:236px;top:487px"><div class="pic"><div role="img" aria-label="Striped red and orange throw pillows" style="width:100px;height:60px;background:linear-gradient(#e3462f,#f4f0ea,#f08a24)"></div><svg width="13" height="11"><path d="M1 2h2l2 6h6l1-4H4" fill="none" stroke="#999"/></svg></div><h4>EXCEPTEUR SINT</h4><p>Lorem ipsum dolor sit amet, consectetur adipiscing elit, sed do eiusmod...</p><div class="price">$29.99</div></div>
<div class="abs card" style="left:389px;top:487px"><div class="pic"><div role="img" aria-label="Folded plaid blankets" style="width:100px;background:linear-gradient(135deg,#2f6fc4,#c8d9ef,#7a8c3a)"></div><svg width="13" height="11"><path d="M1 2h2l2 6h6l1-4H4" fill="none" stroke="#999"/></svg></div><h4>NOSTRUD EXERCITATION</h4><p>Lorem ipsum dolor sit amet, consectetur adipiscing elit, sed do eiusmod...</p><div class="price">$29.99</div></div>
<div class="abs card" style="left:541px;top:487px"><div class="pic"><div role="img" aria-label="Table lamp with cream shade" style="width:60px;background:linear-gradient(#f1e9d6 40%,#8d8d8d)"></div><svg width="13" height="11"><path d="M1 2h2l2 6h6l1-4H4" fill="none" stroke="#999"/></svg></div><h4>EXERCITATION</h4><p>Lorem ipsum dolor sit amet, consectetur adipiscing elit, sed do eiusmod...</p><div class="price">$29.99</div></div>

<div class="abs card" style="left:83px;top:706px"><div class="pic"><div role="img" aria-label="Rolled pink yoga mat" style="width:110px;height:50px;background:linear-gradient(#f06bb8,#d9449c)"></div><svg width="13" height="11"><path d="M1 2h2l2 6h6l1-4H4" fill="none" stroke="#999"/></svg></div><h4>CUPIDATAT</h4><p>Lorem ipsum dolor sit amet, consectetur adipiscing elit, sed do eiusmod...</p><div class="price">$29.99</div></div>
<div class="abs card" style="left:236px;top:706px"><div class="pic"><div role="img" aria-label="Blue enamel flower vase" style="width:45px;background:linear-gradient(#3457a6,#5d86d1,#2b4a91)"></div><svg width="13" height="11"><path d="M1 2h2l2 6h6l1-4H4" fill="none" stroke="#999"/></svg></div><h4>EXCEPTEUR SINT</h4><p>Lorem ipsum dolor sit amet, consectetur adipiscing elit, sed do eiusmod...</p><div class="price">$29.99</div></div>
<div class="abs card" style="left:389px;top:706px"><div class="pic"><div role="img" aria-label="Stack of pink and blue pillows" style="width:90px;height:70px;background:linear-gradient(#e8408c,#f2e6e8,#8fc0e6)"></div><svg width="13" height="11"><path d="M1 2h2l2 6h6l1-4H4" fill="none" stroke="#999"/></svg></div><h4>NOSTRUD EXERCITATION</h4><p>Lorem ipsum dolor sit amet, consectetur adipiscing elit, sed do eiusmod...</p><div class="price">$29.99</div></div>
<div class="abs card" style="left:541px;top:706px"><div class="pic"><div role="img" aria-label="Colourful flower bouquet in clay vase" style="width:60px;background:linear-gradient(#e0357a,#f2a21e 45%,#9a5a2e)"></div><svg width="13" height="11"><path d="M1 2h2l2 6h6l1-4H4" fill="none" stroke="#999"/></svg></div><h4>EXERCITATION</h4><p>Lorem ipsum dolor sit amet, consectetur adipiscing elit, sed do eiusmod...</p><div class="price">$29.99</div></div>

<section class="abs perks">
  <div class="perk" style="left:83px"><div class="ico"><svg width="20" height="14"><rect x="1" y="2" width="11" height="8" fill="#fff"/><path d="M12 5h4l3 3v2h-7z" fill="#fff"/><circle cx="5" cy="11.5" r="2" fill="#fff" stroke="#0355a3"/><circle cx="15" cy="11.5" r="2" fill="#fff" stroke="#0355a3"/></svg></div><div><h5>FREE DELIVERY</h5><p>Lorem ipsum dolor sit amet, consectetur adipiscing elit, sed do eiusmod tempor incididunt ut labore et dolore...</p></div></div>
  <div class="perk-sep" style="left:274px"></div>
  <div class="perk" style="left:290px"><div class="ico"><svg width="18" height="18"><circle cx="9" cy="9" r="8" fill="#fff"/><path d="M5 6c2 0 3 2 2 4s2 3 1 5M11 3c0 2 2 3 4 3" fill="none" stroke="#0355a3" stroke-width="1.5"/></svg></div><div><h5>ANYTIME ANYWERE</h5><p>Lorem ipsum dolor sit amet, consectetur adipiscing elit, sed do eiusmod tempor incididunt ut labore et dolore...</p></div></div>
  <div class="perk-sep" style="left:485px"></div>
  <div class="perk" style="left:503px"><div class="ico"><svg width="20" height="14"><rect x="1" y="1" width="18" height="12" rx="1" fill="none" stroke="#fff" stroke-width="1.5"/><rect x="1" y="4" width="18" height="2.5" fill="#fff"/><rect x="4" y="9" width="6" height="1.5" fill="#fff"/></svg></div><div><h5>SECURE PAYMENT</h5><p>Lorem ipsum dolor sit amet, consectetur adipiscing elit, sed do eiusmod tempor incididunt ut labore et dolore...</p></div></div>
</section>

<footer class="abs footer">
  <div class="abs brand" style="left:83px;top:21px"><span class="name">hollis</span><span class="tag">HOME GOODS</span></div>
  <div class="fcol" style="left:231px"><h6>EXTRAS</h6><ul><li>Specials</li><li>New products</li><li>Best sellers</li><li>Contact us</li><li>Delivery</li></ul></div>
  <div class="fcol" style="left:314px"><h6>INFORMATION</h6><ul><li>Legal Notice</li><li>Terms and conditions</li><li>Privacy Policy</li><li>Returns</li><li>Sitemap</li></ul></div>
  <div class="fcol newsletter" style="left:416px"><h6 style="margin-bottom:4px">NEWSLETTER</h6>Get our recent updates through your email id<input type="text" placeholder="Enter your email id"><span class="btn">SUBSCRIBE</span></div>
  <div class="fcol" style="left:591px;line-height:11px"><h6>CONTACT</h6><div style="font-weight:700;color:#555">HOLLIS</div><div>543#Company Name,Simply,<br>Street Name,City-534</div>
    <div class="contact-line" style="margin-top:5px"><svg width="7" height="7"><path d="M1 1l2 0 1 2-1 1c1 1 1 1 2 2l1-1 2 1v2C4 8 0 4 1 1z" fill="#777"/></svg>01632 960 123</div>
    <div class="contact-line" style="margin-top:4px"><svg width="7" height="6"><rect x="0" y="0" width="7" height="6" fill="#777"/><path d="M0 0l3.5 3L7 0" fill="none" stroke="#f1f1f1" stroke-width=".8"/></svg>support@hollis-home.example</div>
  </div>
</footer>
<div class="abs fbar"></div>
<div class="abs copy">Copyrights © Hollis . 2017 | All rights reserved.</div>
<div class="abs pay">Payment Info :<span class="c"><svg width="14" height="10"><rect x=".5" y=".5" width="13" height="9" rx="1" fill="none" stroke="#555"/><rect x=".5" y="3" width="13" height="2" fill="#555"/></svg></span><span class="c">Monvex</span></div>

</body>
</html>
```